Sophisticated, clean website reflecting my feminine, playful side to sell my abstract art,

I need a website no more than 3 pages to showcase my paintings, a little about me and some contact info. I do abstracts so looking for something a little edgy, yet feminine and current.
Updates

Hi there, These are some artists websites that I Iike: Marnelvoss.com (I like how airy it is) peterwallombry.com garethpolvens.com (I like how it scrolls) I'll need a place for a photo ( a headshot-i do not have it yet so I'll need to be able to upload that later) as well as an area for my bio. Also, it's important that I will be able to upload any new photos and descriptions easily so it should be user friendly. Lastly, I like in a sunny place so would like to have this seem upbeat and playful as that is how i like to paint. thanks-I'm trying to upload my photos now -

Target Market(s)

ppl ages 35-70 who want large scale art for their homes

Industry/Entity Type

art

Coding

Coded - Design and coding required

Number of Pages Required

3 page

Colors

Designer to choose colors to be used in the design.

Requirements
Must have
• photos of my art, a place for my bio, be easy to reach me. tasteful-nothing too "in your face" -my clients are pretty high end and organized. They like clean lines
Nice to have
• sophisticated background, muted tones in the back-similar clean font throughout-no cursive
Should not have
• too many dark areas. Too many blocks of color. Too serious.

```html
<!DOCTYPE html>
<html lang="en">
<head>
<meta charset="utf-8">
<title>Contact – Lena Marchetti</title>
<link rel="stylesheet" href="https://fonts.googleapis.com/css2?family=Oswald:wght@300;400&family=Baloo+2:wght@400&display=swap">
<style>
  :root {
    --ink: #000000;
    --paper: #ffffff;
    --muted: #8a8a8a;
    --rule: #222222;
    --footer: #333333;
  }
  * { box-sizing: border-box; margin: 0; padding: 0; }
  html, body { width: 1200px; height: 752px; overflow: hidden; background: var(--paper); }
  .page { position: relative; width: 1200px; height: 752px; font-family: "Baloo 2", sans-serif; color: var(--ink); }

  .brand { position: absolute; top: 28px; left: 0; width: 1200px; display: flex; justify-content: center; align-items: center; gap: 12px; }
  .brand-mark { width: 40px; height: 58px; background: var(--ink); }
  .brand-name { font-family: "Oswald", sans-serif; font-weight: 300; font-size: 17px; letter-spacing: 0.5px; text-transform: uppercase; color: var(--ink); }
  .brand-rule { position: absolute; top: 109px; left: 514px; width: 172px; border-top: 1px solid var(--rule); }

  .site-nav { position: absolute; top: 131px; left: 0; width: 1200px; display: flex; justify-content: center; gap: 66px; padding-left: 0; }
  .site-nav a { font-family: "Oswald", sans-serif; font-weight: 300; font-size: 20px; color: #222; text-decoration: none; text-transform: uppercase; line-height: 30px; }
  .site-nav a.current { font-weight: 400; color: var(--ink); }

  .contact-form { position: absolute; top: 232px; left: 391px; width: 417px; }
  .field { position: relative; height: 48px; border-bottom: 1px solid var(--rule); }
  .field label { position: absolute; left: 16px; top: 5px; font-size: 13px; color: var(--muted); }
  .field label .req { color: var(--ink); margin-right: 3px; }
  .field.message { height: 83px; }
  .send { display: block; width: 417px; height: 46px; margin-top: 30px; background: var(--ink); color: var(--paper); border: 0; font-family: "Oswald", sans-serif; font-size: 16px; text-transform: uppercase; }
  .form-note { margin-top: 13px; text-align: center; font-size: 12px; color: var(--muted); }

  .social { position: absolute; top: 574px; left: 0; width: 1200px; display: flex; justify-content: center; gap: 28px; }
  .social a { display: flex; align-items: center; gap: 7px; text-decoration: none; color: var(--ink); font-size: 13px; }
  .social .dot { width: 29px; height: 29px; border: 1.3px solid var(--ink); border-radius: 50%; }

  .site-footer { position: absolute; top: 720px; left: 0; width: 1200px; text-align: center; font-size: 12px; color: var(--footer); }
</style>
</head>
<body>
<div class="page">
  <header>
    <div class="brand">
      <span class="brand-mark"></span>
      <span class="brand-name">Lena Marchetti</span>
    </div>
    <div class="brand-rule"></div>
    <nav class="site-nav">
      <a href="#">Gallery</a>
      <a href="#">About</a>
      <a href="#" class="current">Contact</a>
    </nav>
  </header>

  <form class="contact-form">
    <div class="field"><label><span class="req">*</span>First Name</label></div>
    <div class="field"><label><span class="req">*</span>Last Name</label></div>
    <div class="field"><label><span class="req">*</span>Email</label></div>
    <div class="field message"><label><span class="req">*</span>Message</label></div>
    <button type="button" class="send">Send Message</button>
    <p class="form-note">Fields containing (*) are mandatory.</p>
  </form>

  <div class="social">
    <a href="#"><span class="dot"></span>Snapfold</a>
    <a href="#"><span class="dot"></span>Loopit</a>
  </div>

  <footer class="site-footer">©2022 Lena Marchetti Art. All rights reserved.</footer>
</div>
</body>
</html>
```